Design the Business card for NetVaultic

Business card required for a professional Cyber Security business.
Company Logo and Icon has already been provided however I would like other options for the logo and icon to compare to. Alternatively, please refine/enhance the image of the logo.icon I have already provided.

If you are going to use the provided logo and icon, I was thinking that the company raised Logo on White background would serve well on the front of the card. See attached. AND, a large company raised stand-alone icon to appear on black background on the back of the card with tagline 'Cyber Risk Management, Governance and Consulting' or 'Cyber Security for your Business' See attached.
Alternatively, provide your own design for the logo and icon.

Target Market(s)

Enterprise, Government, Financial.

Contact Information for Business Card

Tavin Orloweth
Founder and CEO

Email Address
Mobile Number
Website URL
LinkedIn URL

Logo Text

NetVaultic - see attached example of logo

Font styles to use
Other font styles liked:
• Berlin Sans FB

Requirements
Must have
• Clean large and bold icon on the back with tagline.
• Horizontal alignment,
Nice to have
• Round edges.
• Raised Logo/Icon
Should not have
• An unprofessional look and feel.

```html
<!DOCTYPE html>
<html lang="en">
<head>
<meta charset="utf-8">
<title>NetVaultic Business Card</title>
<link href="https://fonts.googleapis.com/css2?family=Roboto:wght@400;500&family=Mulish:wght@400&display=swap" rel="stylesheet">
<style>
  :root {
    --backdrop: #3b3430;
    --card: #1d2125;
    --card-edge: #15181b;
    --brand-blue: #1a7fd4;
    --accent-gold: #f2b21b;
    --text-light: #f1f3f5;
    --text-muted: #a9afb5;
    --divider: #5a6068;
  }
  * { margin: 0; padding: 0; box-sizing: border-box; }
  html, body { width: 1200px; height: 769px; overflow: hidden; }
  body {
    background: var(--backdrop);
    display: flex;
    align-items: center;
    justify-content: center;
    gap: 48px;
    font-family: "Roboto", Arial, sans-serif;
  }
  .card {
    width: 540px;
    height: 310px;
    background: var(--card);
    border-radius: 12px;
    box-shadow: 0 10px 28px rgba(0,0,0,.45);
    position: relative;
    overflow: hidden;
  }
  /* Back of card */
  .card-back {
    display: flex;
    flex-direction: column;
    align-items: center;
    justify-content: center;
    gap: 22px;
  }
  .brand-mark {
    display: flex;
    align-items: center;
    gap: 14px;
  }
  .brand-dot {
    border-radius: 50%;
    background: var(--brand-blue);
  }
  .card-back .brand-dot { width: 40px; height: 40px; }
  .brand-name {
    color: var(--brand-blue);
    font-weight: 500;
    letter-spacing: .5px;
  }
  .card-back .brand-name { font-size: 50px; }
  .tagline {
    font-family: "Mulish", Arial, sans-serif;
    color: var(--text-muted);
    font-size: 17px;
    letter-spacing: .2px;
  }
  /* Front of card */
  .card-front .brand-mark {
    position: absolute;
    top: 62px;
    left: 70px;
  }
  .card-front .brand-dot { width: 34px; height: 34px; }
  .card-front .brand-name { font-size: 54px; }
  .contact-row {
    position: absolute;
    left: 52px;
    right: 30px;
    top: 175px;
    display: flex;
    align-items: flex-start;
  }
  .identity {
    text-align: right;
    padding-right: 18px;
    width: 200px;
  }
  .person-name {
    color: var(--brand-blue);
    font-size: 20px;
    font-weight: 500;
    text-transform: uppercase;
  }
  .person-role {
    color: var(--accent-gold);
    font-size: 16px;
    text-transform: uppercase;
    margin-top: 4px;
  }
  .divider {
    width: 1px;
    height: 96px;
    background: var(--divider);
    margin-top: 2px;
  }
  .details {
    list-style: none;
    padding-left: 18px;
    display: flex;
    flex-direction: column;
    gap: 5px;
    margin-top: 6px;
  }
  .details li {
    display: flex;
    align-items: center;
    gap: 9px;
    color: var(--text-light);
    font-size: 15px;
  }
  .details svg { width: 13px; height: 13px; flex: none; }
</style>
</head>
<body>
  <section class="card card-back">
    <div class="brand-mark">
      <span class="brand-dot"></span>
      <span class="brand-name">NetVaultic</span>
    </div>
    <p class="tagline">Cyber Risk Management, Governance &amp; Consulting</p>
  </section>

  <section class="card card-front">
    <div class="brand-mark">
      <span class="brand-dot"></span>
      <span class="brand-name">NetVaultic</span>
    </div>
    <div class="contact-row">
      <div class="identity">
        <p class="person-name">Tavin Orloweth</p>
        <p class="person-role">Founder &amp; CEO</p>
      </div>
      <span class="divider"></span>
      <ul class="details">
        <li>
          <svg viewBox="0 0 14 14" aria-hidden="true"><rect x="3.5" y="0.8" width="7" height="12.4" rx="1.4" fill="none" stroke="#1a7fd4" stroke-width="1.5"/><circle cx="7" cy="11" r=".8" fill="#1a7fd4"/></svg>
          555 014 2290
        </li>
        <li>
          <svg viewBox="0 0 14 14" aria-hidden="true"><rect x="0.5" y="2.5" width="13" height="9" rx="1" fill="#1a7fd4"/><path d="M1 3.2 7 8l6-4.8" fill="none" stroke="#1d2125" stroke-width="1.2"/></svg>
          tavin@netvaultic.com
        </li>
        <li>
          <svg viewBox="0 0 14 14" aria-hidden="true"><circle cx="7" cy="7" r="6" fill="none" stroke="#1a7fd4" stroke-width="1.5"/><path d="M1 7h12M7 1c-3 3.5-3 8.5 0 12M7 1c3 3.5 3 8.5 0 12" fill="none" stroke="#1a7fd4" stroke-width="1"/></svg>
          www.netvaultic.com
        </li>
        <li>
          <svg viewBox="0 0 14 14" aria-hidden="true"><circle cx="7" cy="7" r="6.5" fill="#1a7fd4"/></svg>
          netvaultic
        </li>
      </ul>
    </div>
  </section>
</body>
</html>
```